Corvane Business Cards

Front of business card will have logo, name, address, & telephone number. Back of card will have a list of services provided - Roads, Substation Pads, Temporary Pads, Site Pads, Land Leveling, Powerline Row Cleaning, Land Clearing, Gates, Fencing, Construction Entrances, Excavation, Trenching, Underground Utilities, Directional Boring, Pile Driving. We are a construction company that uses heavy equipment like bulldozers, motor graders/blades, dump trucks, backhoes, hydro axes, & skid loaders. We build roads, pads, & install electric utility lines & waterlines underground. This logo is new. The word "Construction" can be smaller as uploaded 2 example edited logos. We will be using this card design for many employees.
Target Market(s)
Industrial Electric Powerline, Wind Turbine, Solar Panel, & Water Utility companies.
Contact Information for Business Card
Name/Position - Dwayne Halster - Owner
Address: 4875 FM 309
Merkel, TX 79412
Phone number - (325) 482-5096

```html
<!DOCTYPE html>
<html lang="en">
<head>
<meta charset="utf-8">
<title>Corvane Construction – Business Card</title>
<link href="https://fonts.googleapis.com/css2?family=Arimo:wght@400;700&display=swap" rel="stylesheet">
<style>
  :root {
    --page-bg: #e9e7e6;
    --maroon: #4b1420;
    --maroon-deep: #3d0f19;
    --maroon-light: #5e1a28;
    --ink: #3a0e17;
    --text-grey: #4a4a4a;
    --rule: #9a9a9a;
    --paper: #ffffff;
  }
  * { box-sizing: border-box; margin: 0; padding: 0; }
  html, body {
    width: 1200px;
    height: 1015px;
    overflow: hidden;
    background: var(--page-bg);
    font-family: "Arimo", Arial, sans-serif;
  }
  .sheet {
    position: relative;
    width: 1200px;
    height: 1015px;
  }
  .card {
    position: absolute;
    left: 250px;
    width: 700px;
    height: 400px;
    box-shadow: 0 10px 28px rgba(0,0,0,0.22);
  }
  .card--back {
    top: 70px;
    background: var(--maroon);
    display: flex;
    align-items: center;
    justify-content: center;
    overflow: hidden;
  }
  .back-pattern {
    position: absolute;
    inset: 0;
    background: linear-gradient(135deg, var(--maroon-light), var(--maroon-deep));
  }
  .back-mark {
    position: relative;
    color: var(--paper);
    font-weight: 700;
    font-size: 30px;
    letter-spacing: 1px;
  }
  .card--front {
    top: 545px;
    background: var(--paper);
    display: flex;
    align-items: center;
  }
  .front-brand {
    width: 390px;
    padding-left: 60px;
    color: var(--ink);
    font-weight: 700;
  }
  .front-brand .brand-name {
    font-size: 64px;
    line-height: 1;
    letter-spacing: 2px;
  }
  .front-brand .brand-sub {
    font-size: 30px;
    letter-spacing: 3px;
    margin-top: 10px;
  }
  .divider {
    width: 1px;
    height: 150px;
    background: var(--rule);
  }
  .contact {
    padding-left: 34px;
    color: var(--text-grey);
  }
  .contact .person {
    color: var(--ink);
    font-weight: 700;
    font-size: 24px;
    letter-spacing: 0.5px;
  }
  .contact .role {
    font-size: 15px;
    margin: 2px 0 0 22px;
  }
  .contact .phone {
    color: var(--ink);
    font-weight: 700;
    font-size: 19px;
    margin: 14px 0 0 44px;
  }
  .contact .address {
    font-size: 16px;
    line-height: 1.3;
    margin: 12px 0 0 70px;
  }
</style>
</head>
<body>
<main class="sheet">
  <section class="card card--back">
    <div class="back-pattern" role="img" aria-label="Repeating embossed company emblem pattern in deep maroon"></div>
    <div class="back-mark">Corvane</div>
  </section>

  <section class="card card--front">
    <div class="front-brand">
      <div class="brand-name">CORVANE</div>
      <div class="brand-sub">CONSTRUCTION</div>
    </div>
    <div class="divider"></div>
    <div class="contact">
      <div class="person">DWAYNE HALSTER</div>
      <div class="role">Owner</div>
      <div class="phone">P: (325) 482-5096</div>
      <div class="address">4875 FM 309<br>Merkel, TX 79412</div>
    </div>
  </section>
</main>
</body>
</html>
```